Creative, fresh business card design for Ripplecraft Facades

We need a fresh, creative business card design for Ripplecraft Facades. We are the manufacturer of Ripplecraft Facades in Australia. Wall panels are 2400 x 1200mm panels made from MDF and feature 3D patterns on the face of the panel. The colours to be used are green, silver/grey and white RGB
Red 187
Green 207
Blue 65.

An idea is to possibly use a watermark of one of our designs as a background (like on the "Grids" design on the left hand side of page 2 of our brochure).

Target Market(s)

Interior designers, architects, builders and home renovators

Industry/Entity Type

Business

Contact Information for Business Card

Details to go on the card are:
Our logo (attached),
Slogan: "Decorative panels for interiors and exteriors",
Contact name,
Position,
Mobile phone number,
Business address,
Business phone,
Business fax,
Website and
Email address.

I have attached a few images of our panels and our brochure for reference.

The colours of the business card should feature our logo colours which are: RGB
Red 187
Green 207
Blue 65

Requirements
Must have
• Very modern fonts and design. Some of the designs shown especially the "Prisms" design which is a popular design.
Nice to have
• Creative but simple design. Very contemporary.
Should not have
• Anything ornate or old fashioned.

```html
<!DOCTYPE html>
<html lang="en">
<head>
<meta charset="utf-8">
<title>Ripplecraft Facades — Business Card</title>
<link rel="stylesheet" href="https://fonts.googleapis.com/css2?family=Open+Sans:wght@400;600;700&display=swap">
<style>
  :root {
    --lime: rgb(187, 207, 65);
    --lime-card: #c0d72f;
    --silver: #8e8f92;
    --ink: #3d3d3f;
    --paper: #ffffff;
    --backdrop: #5b4b3d;
  }
  * { margin: 0; padding: 0; box-sizing: border-box; }
  html, body { width: 1200px; height: 987px; overflow: hidden; }
  body {
    background: var(--backdrop);
    font-family: "Open Sans", Arial, sans-serif;
    position: relative;
  }
  .card {
    position: absolute;
    left: 293px;
    width: 615px;
    height: 352px;
  }
  .card--front { top: 130px; background: var(--paper); }
  .card--back  { top: 505px; background: var(--lime-card); }

  /* front */
  .accent-bar {
    position: absolute; left: 0; top: 45px;
    width: 11px; height: 30px; background: var(--lime);
  }
  .accent-bar--grey { top: 76px; height: 11px; background: var(--silver); }
  .person { position: absolute; left: 43px; top: 44px; }
  .person__name {
    color: var(--lime); font-weight: 700; font-size: 21px;
    letter-spacing: 0.2px; line-height: 1.1;
  }
  .person__role { color: var(--silver); font-size: 16px; margin-top: 3px; }

  .address {
    position: absolute; left: 43px; top: 163px;
    color: var(--ink); font-size: 16px; line-height: 23px;
  }
  .contacts {
    position: absolute; left: 43px; top: 217px;
    list-style: none; color: var(--ink); font-size: 16px;
  }
  .contacts li { display: flex; align-items: center; height: 23.5px; }
  .contacts svg { width: 16px; height: 16px; margin-right: 10px; fill: var(--lime); flex: none; }

  .brand { position: absolute; display: flex; flex-direction: column; }
  .brand__lockup { display: flex; align-items: center; }
  .brand__mark { width: 26px; height: 26px; background: var(--lime); margin-right: 9px; flex: none; }
  .brand__name { font-weight: 600; white-space: nowrap; }
  .brand__tagline {
    font-size: 12.5px; letter-spacing: 2.2px; line-height: 16px;
    text-align: center; margin-top: 12px;
  }
  .card--front .brand { right: 44px; top: 170px; width: 240px; align-items: center; }
  .card--front .brand__name { color: var(--silver); font-size: 20px; }
  .card--front .brand__tagline { color: var(--silver); }

  .card--back .brand { left: 0; right: 0; top: 112px; align-items: center; }
  .card--back .brand__mark { background: var(--paper); width: 38px; height: 38px; margin-right: 12px; }
  .card--back .brand__name { color: var(--paper); font-size: 30px; }
  .card--back .brand__tagline { color: var(--paper); font-size: 13.5px; margin-top: 16px; }
  .website {
    position: absolute; left: 0; right: 0; top: 236px;
    text-align: center; color: var(--paper); font-size: 15px; letter-spacing: 3px;
  }
</style>
</head>
<body>
  <section class="card card--front">
    <span class="accent-bar"></span>
    <span class="accent-bar accent-bar--grey"></span>
    <div class="person">
      <p class="person__name">LIAM HARROW</p>
      <p class="person__role">CEO&amp;Founder</p>
    </div>
    <address class="address" style="font-style:normal">
      42 Tallowwood Drive<br>
      Newcastle, NSW 2300
    </address>
    <ul class="contacts">
      <li>
        <svg viewBox="0 0 16 16" aria-hidden="true"><path d="M3.6 1.2l2.3 2.6-1.3 1.9c.9 2 2.4 3.5 4.2 4.3l1.8-1.4 2.6 2.3-1.2 2.5C6.4 13.3 2.3 9.3 1.2 3.8z"/></svg>
        (02) 4960 1187
      </li>
      <li>
        <svg viewBox="0 0 16 16" aria-hidden="true"><path d="M4 1h8v4H4zM1 6h14v6h-2.5v-2h-9v2H1zM4.5 11h7v4h-7z"/></svg>
        (02) 4960 1188
      </li>
      <li>
        <svg viewBox="0 0 16 16" aria-hidden="true"><path d="M1 3.5h14v1L8 9 1 4.5zM1 6l7 4.5L15 6v7H1z"/></svg>
        lharrow@ripplecraftfacades.com
      </li>
      <li>
        <svg viewBox="0 0 16 16" aria-hidden="true"><path d="M8 1a7 7 0 100 14A7 7 0 008 1zm-2 3.5c1.2-.3 2.4.4 2.2 1.5-.2.9-1.6.9-1.5 2 .1 1 1.6 1.3 1.5 2.6l-.7 2.8C5 12.8 3 10.7 3 8c0-1.4.9-2.8 3-3.5zm4.5 1.2c1 .2 2.2 1 2.5 2.4-.8.3-1.8 0-2.3-.7z"/></svg>
        www.ripplecraftfacades.com
      </li>
    </ul>
    <div class="brand">
      <div class="brand__lockup">
        <span class="brand__mark"></span>
        <span class="brand__name">Ripplecraft Facades</span>
      </div>
      <p class="brand__tagline">decorative panels for<br>interiors &amp; landscapes</p>
    </div>
  </section>

  <section class="card card--back">
    <div class="brand">
      <div class="brand__lockup">
        <span class="brand__mark"></span>
        <span class="brand__name">Ripplecraft Facades</span>
      </div>
      <p class="brand__tagline">decorative panels for<br>interiors &amp; landscapes</p>
    </div>
    <p class="website">www.ripplecraftfacades.com</p>
  </section>
</body>
</html>
```